Card Design for my dog training business Brightpaw Obedience

Need a business card design for my dog training business with my new logo. Want the card to come off professional yet fun. Want it to be very eye catchy as well. I normally have these at vet clinics, pet stores, and groomers. so need it to look better than my competitors.
Target Market(s)
dog owners
Industry/Entity Type
Dog Training
Contact Information for Business Card
needs logo, my name and info
Font styles to use
Serif
Colors
0255a3
ffffff
ec1f27
000000
333333
fbfbfb
Requirements
Must have
- Brightpaw Obedience
- Felix Orland
- 415 903 2276
- info@brightpawobedience.example
- www.brightpawobedience.example

```html
<!DOCTYPE html>
<html lang="en">
<head>
<meta charset="utf-8">
<title>Brightpaw Obedience – Business Card</title>
<link href="https://fonts.googleapis.com/css2?family=Montserrat:wght@400;500;600&display=swap" rel="stylesheet">
<style>
  :root {
    --backdrop: #d9d6d1;
    --card-dark: #2b2d31;
    --card-dark-deep: #1e1f22;
    --brand-blue: #1a9fdc;
    --ink-blue: #0255a3;
    --paper: #fbfbfb;
    --text-light: #f2f2f2;
    --text-logo: #e6e6e6;
  }
  * { margin: 0; padding: 0; box-sizing: border-box; }
  html, body {
    width: 1200px; height: 894px; overflow: hidden;
    background: var(--backdrop);
    font-family: "Montserrat", sans-serif;
  }
  .stage {
    width: 1200px; height: 894px;
    display: flex; justify-content: center; align-items: center; gap: 80px;
  }
  .card {
    width: 400px; height: 700px; position: relative; overflow: hidden;
    border-radius: 4px;
    box-shadow: 0 10px 30px rgba(0,0,0,.25);
  }
  /* Front */
  .card-front { background: var(--paper); }
  .front-top {
    position: absolute; inset: 0 0 auto 0; height: 390px;
    background: linear-gradient(160deg, var(--card-dark) 0%, var(--card-dark-deep) 100%);
    padding: 70px 44px 0;
  }
  .holder-name {
    color: var(--brand-blue); font-weight: 600; font-size: 25px;
    letter-spacing: 2px; text-transform: uppercase; margin-bottom: 26px;
  }
  .contact-list { list-style: none; }
  .contact-list li {
    display: flex; align-items: center; gap: 14px;
    color: var(--text-light); font-size: 14.5px; letter-spacing: .3px;
    margin-bottom: 9px;
  }
  .contact-list svg { width: 16px; height: 16px; flex: none; }
  .illustration {
    position: absolute; left: 40px; top: 280px; width: 340px; height: 300px;
  }
  .tagline {
    position: absolute; left: 0; right: 0; bottom: 46px;
    text-align: center; color: var(--brand-blue);
    font-size: 17px; line-height: 1.35;
  }
  /* Back */
  .card-back {
    background: linear-gradient(160deg, var(--card-dark) 0%, var(--card-dark-deep) 100%);
    display: flex; align-items: center; justify-content: center;
  }
  .brand-lockup { display: flex; align-items: center; gap: 12px; }
  .brand-dot {
    width: 14px; height: 14px; border-radius: 50%; background: var(--text-logo);
  }
  .brand-name {
    color: var(--text-logo); font-weight: 500; font-size: 24px;
    letter-spacing: 1.5px; text-transform: uppercase;
  }
</style>
</head>
<body>
<main class="stage">
  <section class="card card-front">
    <div class="front-top">
      <h1 class="holder-name">Felix Orland</h1>
      <ul class="contact-list">
        <li>
          <svg viewBox="0 0 16 16" aria-hidden="true"><path d="M4 1.5 6 4.5 4.8 6a8 8 0 0 0 5.2 5.2L11.5 10l3 2-1.3 2.4C7.5 14.5 1.5 8.5 1.6 2.8Z" fill="var(--brand-blue)"/></svg>
          415 903 2276
        </li>
        <li>
          <svg viewBox="0 0 16 16" aria-hidden="true"><rect x="1" y="3" width="14" height="10" rx="1" fill="var(--brand-blue)"/><path d="M1.5 3.5 8 9l6.5-5.5" stroke="var(--card-dark)" stroke-width="1.3" fill="none"/></svg>
          info@brightpawobedience.example
        </li>
        <li>
          <svg viewBox="0 0 16 16" aria-hidden="true"><circle cx="8" cy="8" r="6.5" fill="var(--brand-blue)"/><path d="M1.5 8h13M8 1.5v13M3 4.5h10M3 11.5h10" stroke="var(--card-dark)" stroke-width="1" fill="none"/><ellipse cx="8" cy="8" rx="3" ry="6.5" stroke="var(--card-dark)" stroke-width="1" fill="none"/></svg>
          www.brightpawobedience.example
        </li>
      </ul>
    </div>
    <svg class="illustration" viewBox="0 0 340 300" role="img" aria-label="Blue line illustration of two dog heads side by side">
      <defs>
        <linearGradient id="dogTone" x1="0" y1="0" x2="1" y2="1">
          <stop offset="0" stop-color="#4a8fd6"/>
          <stop offset="1" stop-color="#0255a3"/>
        </linearGradient>
      </defs>
      <rect x="0" y="0" width="340" height="300" rx="40" fill="url(#dogTone)"/>
    </svg>
    <p class="tagline">“Training dogs across Texas<br>one dog at a time.”</p>
  </section>

  <section class="card card-back">
    <div class="brand-lockup">
      <span class="brand-dot" aria-hidden="true"></span>
      <span class="brand-name">Brightpaw Obedience</span>
    </div>
  </section>
</main>
</body>
</html>
```